Pizza Box 10" x 10" - color: White

Custom design, utilizing CrustVarko Logo and include the following information on the Pizza Box:

1. Custom Crafted Pizza with Quality Ingredients.
2. [....Get Your GAME ON] to be placed on the front flap and seen when the
box is opened.
3. You"ll miss 100% of the Pizza you don't eat.

4. Visit www.lumacartonworks.com for additional design resource information. Go to site and then click on ORDERING to access.

5. The 10" x 10" Pizza Box is to be in the color WHITE.
6. Use colors Black and Red. no generic images. no food pics. I am looking for a clean and cool design.

Target Market(s)

Age 16 - 36 years

Industry/Entity Type

American Restaurant

Font styles to use
Sans Serif

Colors
ec1f27
000000
ffffff

Requirements
Must have
• Color Red and Black.
• Logo on Top and all sides of the Pizza Box.
Nice to have
• A Creative design that does not look generic.
Should not have
• No food images.

```html
<!DOCTYPE html>
<html lang="en">
<head>
<meta charset="utf-8">
<title>CrustVarko Pizza Box Lid</title>
<link rel="stylesheet" href="https://fonts.googleapis.com/css2?family=Russo+One&family=Oswald:wght@500;700&display=swap">
<style>
  :root {
    --red: #ec1f27;
    --black: #000000;
    --white: #ffffff;
    --backdrop: #ababab;
    --ink: #1a1a1a;
  }
  html, body {
    margin: 0;
    padding: 0;
    overflow: hidden;
  }
  body {
    width: 1200px;
    height: 691px;
    background: var(--backdrop);
    display: flex;
    align-items: center;
    justify-content: center;
  }
  .box-lid {
    width: 560px;
    height: 560px;
    display: block;
    box-shadow: 0 2px 6px rgba(0,0,0,0.15);
  }
  .lid-paper { fill: var(--white); }
  .band-black { fill: var(--black); }
  .rule-black { fill: var(--black); }
  .band-red { fill: var(--red); }
  .rule-red { fill: var(--red); }
  .corner-flag { fill: var(--red); }
  .flag-small {
    font-family: "Oswald", sans-serif;
    font-weight: 500;
    font-size: 15px;
    fill: var(--white);
    letter-spacing: 0.5px;
  }
  .flag-big {
    font-family: "Oswald", sans-serif;
    font-weight: 700;
    font-size: 40px;
    fill: var(--white);
  }
  .flag-note {
    font-family: "Oswald", sans-serif;
    font-weight: 500;
    font-size: 10px;
    fill: var(--white);
    letter-spacing: 0.3px;
  }
  .brand-dot { fill: var(--red); }
  .brand-name {
    font-family: "Russo One", sans-serif;
    font-size: 52px;
    fill: var(--ink);
  }
  .tagline {
    font-family: "Oswald", sans-serif;
    font-weight: 500;
    font-size: 15px;
    fill: var(--white);
    letter-spacing: 1px;
  }
  .game-on {
    font-family: "Oswald", sans-serif;
    font-weight: 700;
    font-size: 13px;
    fill: var(--white);
    letter-spacing: 0.5px;
  }
  .game-dot { fill: none; stroke: var(--white); stroke-width: 2; }
</style>
</head>
<body>
  <svg class="box-lid" viewBox="0 0 560 560" role="img" aria-label="CrustVarko pizza box lid">
    <rect class="lid-paper" x="0" y="0" width="560" height="560"/>

    <!-- top black band and accent rule -->
    <polygon class="band-black" points="0,0 560,0 560,40 0,98"/>
    <polygon class="rule-black" points="0,110 420,62 420,68 0,117"/>

    <!-- corner flag with slogan -->
    <polygon class="corner-flag" points="340,0 560,0 560,175"/>
    <g transform="translate(490,50) rotate(38.5)">
      <text class="flag-small" x="0" y="-20" text-anchor="middle">YOU'LL MISS</text>
      <text class="flag-big" x="0" y="16" text-anchor="middle">100%</text>
      <text class="flag-note" x="0" y="30" text-anchor="middle">OF THE PIZZA YOU DON'T EAT</text>
    </g>

    <!-- brand -->
    <g class="brand">
      <circle class="brand-dot" cx="78" cy="272" r="27"/>
      <text class="brand-name" x="118" y="291" textLength="320" lengthAdjust="spacingAndGlyphs">CrustVarko</text>
    </g>

    <!-- bottom red band and accent rule -->
    <polygon class="rule-red" points="0,420 560,320 560,327 0,428"/>
    <polygon class="band-red" points="0,442 560,342 560,560 0,560"/>

    <text class="tagline" x="290" y="490" text-anchor="middle" transform="rotate(-5 290 490)">CUSTOM CRAFTED PIZZA WITH QUALITY INGREDIENTS.</text>

    <g class="game-on-mark">
      <circle class="game-dot" cx="232" cy="532" r="7"/>
      <text class="game-on" x="244" y="537">GET YOUR GAME ON</text>
    </g>
  </svg>
</body>
</html>
```